Creation of an elegant and modern turnkey Shopify website

Hello,

We are a new company specializing in the sale of above-ground pools. We want to create a turnkey website, ideally using Shopify. For now, we need a "showcase" site, not an e-commerce platform, with four tabs:

Home Page (an overall presentation of the company)
Our Products (an overview of all the above-ground pools we sell)
Our Projects (a page inspired by Instagram to showcase photos of our future projects)
Contact (a page with all our contact information and a contact form)

We are looking to create a highly visual, elegant, and modern website with vibrant splashes of color. We will provide the text, photos (along with instructions on where to place them on each page), and all other necessary information as attachments.

Thank you in advance for your proposals!

The Brisa Lagoon Team

Target Market(s)

Targeted at Swiss customers (a translator will need to be installed for different languages)

Industry/Entity Type

Sale of customised above-ground pools

Coding

Coded - Design and coding required

Font styles to use
Sans Serif

Colors
0094D4
00A9DD
6FCCEA
C7EBF8
E9F6FB
00AB8E
00BBA5
67D7C9
C6EFE9
E9F9F6

Requirements
Must have
• A stunning, elegant and modern look
Nice to have
• Inspiration from the colors of our logo throughout the site, but in an elegant way
Should not have
• An overly classic look for swimming pool sites

```html
<!DOCTYPE html>
<html lang="en">
<head>
<meta charset="utf-8">
<title>Brisa Lagoon – Contact</title>
<link href="https://fonts.googleapis.com/css2?family=Mulish:wght@300;400;500;600;700&display=swap" rel="stylesheet">
<style>
:root{
  --cyan:#00e1f5;
  --cyan-soft:#cdf9fd;
  --ink:#111;
  --white:#fff;
  --grey:#7f7f7f;
  --grey-dark:#6c6c6c;
  --button-grey:#6e6e6e;
  --field-text:#8a8a8a;
}
*{box-sizing:border-box;margin:0;padding:0}
html,body{width:1200px;height:2498px;overflow:hidden;background:var(--white)}
body{font-family:"Mulish",sans-serif;color:var(--ink);position:relative}
.abs{position:absolute}

/* header */
.site-header{position:absolute;left:0;top:0;width:1200px;height:110px;background:var(--white);z-index:3}
.brand-badge{position:absolute;left:52px;top:-16px;width:216px;height:216px;border-radius:50%;background:var(--white);z-index:4;display:flex;flex-direction:column;align-items:center;justify-content:center;padding-top:16px}
.brand-badge span{font-weight:300;color:var(--cyan);font-size:36px;line-height:1;letter-spacing:3px}
.main-nav a{position:absolute;top:48px;font-size:16px;font-weight:500;color:var(--ink);text-decoration:none;letter-spacing:.2px;white-space:nowrap}
.main-nav a.active{color:var(--cyan)}
.main-nav a.active::after{content:"";position:absolute;left:-6px;right:-6px;top:30px;height:3px;background:var(--cyan)}
.lang-switch{position:absolute;left:1067px;top:37px;width:60px;height:41px;border:1px solid #ccc;border-radius:6px;background:#fafafa}

/* hero */
.hero{position:absolute;left:0;top:110px;width:1200px;height:701px;background:linear-gradient(180deg,#7fb6e6 0%,#9cc7ea 25%,#4e5d74 45%,#3c4a62 70%,#5aa84a 88%,#4d9a3e 100%)}
.hero h1{position:absolute;left:-50px;top:372px;width:1300px;text-align:center;color:var(--white);font-weight:600;font-size:39px;line-height:45px;letter-spacing:.3px}
.btn{position:absolute;display:flex;align-items:center;border-radius:30px;color:var(--white);font-weight:700;font-size:16px;white-space:nowrap}
.btn .arrow{width:32px;height:32px;border-radius:50%;background:var(--white);display:flex;align-items:center;justify-content:center;margin-left:10px}
.hero .btn{left:539px;top:531px;width:221px;height:56px;background:var(--cyan);padding-left:34px}
.dots{position:absolute;top:652px;left:600px;display:flex;gap:13px;align-items:center}
.dots i{display:block;width:11px;height:11px;border-radius:50%;background:#c9c9c9}
.dots i.on{width:27px;height:5px;border-radius:3px;background:var(--white)}

/* contact intro */
.section-title{position:absolute;left:0;top:900px;width:1200px;text-align:center;font-size:48px;font-weight:500;letter-spacing:.5px}
.title-rule{position:absolute;left:542px;top:972px;width:117px;height:2px;background:var(--ink)}
.intro{position:absolute;left:120px;top:1010px;width:970px;text-align:center;font-size:31px;line-height:36px;font-weight:400}

/* contact panel */
.info-panel{position:absolute;left:77px;top:1238px;width:457px;height:790px;background:linear-gradient(160deg,#9fb9bb 0%,#7fa3a6 45%,#8aa3a4 70%,#6f8c8f 100%)}
.info-item{position:absolute;left:78px;display:flex;align-items:center}
.info-item .icon{width:72px;height:72px;border-radius:50%;background:var(--cyan);display:flex;align-items:center;justify-content:center;flex:none}
.info-item .text{margin-left:20px;color:var(--white);font-size:19px;line-height:25px;white-space:nowrap}
.info-item .text strong{font-weight:500;font-size:21px;display:block}
.form-panel{position:absolute;left:534px;top:1238px;width:591px;height:790px;background:var(--cyan-soft)}
.field-label{position:absolute;font-size:14px;font-weight:600;letter-spacing:.2px;white-space:nowrap}
.field{position:absolute;background:var(--white);font-size:14px;color:var(--field-text);padding:13px 14px;height:45px;white-space:nowrap}
.field.unit{text-align:right}
.submit{left:728px;top:1863px;width:198px;height:58px;background:var(--button-grey);padding-left:30px}
.submit .arrow{background:var(--cyan);margin-left:18px}

/* footer */
.site-footer{position:absolute;left:0;top:2110px;width:1200px;height:336px;background:var(--grey);color:var(--white)}
.footer-brand{position:absolute;left:112px;top:80px;font-weight:300;font-size:48px;line-height:58px;color:var(--white);letter-spacing:3px}
.footer-col h3{position:absolute;font-size:21px;font-weight:500;top:65px;white-space:nowrap}
.footer-col h3::after{content:"";position:absolute;left:0;top:34px;width:36px;height:2px;background:var(--cyan)}
.quick-links{position:absolute;left:402px;top:0;width:180px;height:260px;list-style:none}
.quick-links li{position:absolute;left:0;font-size:14px;line-height:18px;white-space:nowrap}
.quick-links li::before{content:"›";color:var(--cyan);margin-right:10px;font-size:16px}
.f-contact{position:absolute;display:flex;align-items:flex-start;font-size:13.5px;line-height:16px;white-space:nowrap}
.f-contact .box{width:29px;height:29px;border:1.5px solid var(--white);border-radius:4px;display:flex;align-items:center;justify-content:center;margin-right:17px;flex:none}
.newsletter p{position:absolute;left:886px;top:148px;width:230px;font-size:13.5px;line-height:18px}
.newsletter .input{position:absolute;left:886px;top:192px;width:218px;height:34px;background:var(--white)}
.newsletter .sub{position:absolute;left:886px;top:235px;width:109px;height:33px;background:var(--cyan);font-size:12px;display:flex;align-items:center;justify-content:center}
.bottom-bar{position:absolute;left:0;top:2446px;width:1200px;height:52px;background:var(--grey-dark);color:var(--white)}
.bottom-bar p{position:absolute;left:78px;top:17px;font-size:13.5px;white-space:nowrap}
.social{position:absolute;top:9px;width:31px;height:33px;border:1.5px solid var(--white);border-radius:4px}
</style>
</head>
<body>

<header class="site-header">
  <nav class="main-nav">
    <a class="active" style="left:553px">HOME</a>
    <a style="left:634px">OUR PRODUCTS</a>
    <a style="left:790px">OUR PROJECTS</a>
    <a style="left:940px">CONTACT US</a>
  </nav>
  <div class="lang-switch">
    <svg width="60" height="41" viewBox="0 0 60 41">
      <rect x="8" y="12" width="30" height="18" fill="#1f3c8c"/>
      <path d="M8 21h30M23 12v18" stroke="#fff" stroke-width="6"/>
      <path d="M8 21h30M23 12v18" stroke="#d8232a" stroke-width="3"/>
      <path d="M42 18h10l-5 7z" fill="#777"/>
    </svg>
  </div>
</header>
<div class="brand-badge"><span>BRISA</span><span style="margin-top:8px">LAGOON</span></div>

<section class="hero" role="img" aria-label="Photo of a composite wood above-ground pool with glass wall, waterfall and steps on a green lawn">
  <h1>TRANSFORM YOUR<br>GARDEN WITH OUR PREMIUM<br>ABOVE-GROUND POOLS!</h1>
  <div class="btn">OUR PRODUCTS<span class="arrow"><svg width="16" height="12" viewBox="0 0 16 12"><path d="M2 2l4 4-4 4M8 2l4 4-4 4" fill="none" stroke="#00e1f5" stroke-width="2"/></svg></span></div>
  <div class="dots"><i class="on"></i><i></i><i></i><i></i></div>
</section>

<h2 class="section-title">CONTACT US</h2>
<div class="title-rule"></div>
<p class="intro">We would be delighted to advise you. Feel free to reach out to us for any inquiries or to get a personalized quote. We look forward to helping you transform your outdoor space into a true haven of peace and relaxation.</p>

<aside class="info-panel" role="img" aria-label="Photo of legs and a sun hat by the pool, with a soft teal overlay">
  <div class="info-item" style="top:112px">
    <div class="icon"><svg width="30" height="40" viewBox="0 0 30 40"><path d="M15 2C8 2 3 7 3 14c0 9 12 24 12 24s12-15 12-24C27 7 22 2 15 2z" fill="#fff"/><circle cx="15" cy="14" r="5" fill="#00e1f5"/></svg></div>
    <div class="text" style="margin-top:4px">BRISA LAGOON<br>Marco Lehner<br>Rue des Tilleuls 27<br>1860 Aigle</div>
  </div>
  <div class="info-item" style="top:297px">
    <div class="icon"><svg width="36" height="36" viewBox="0 0 36 36"><path d="M8 4l6 6-3 4c2 5 6 9 11 11l4-3 6 6-4 5C16 32 4 20 3 8z" fill="#fff"/><path d="M21 6a10 10 0 0 1 9 9M21 11a5 5 0 0 1 4 4" fill="none" stroke="#fff" stroke-width="2.5"/></svg></div>
    <div class="text"><strong>CALL US</strong>079 555 01 23</div>
  </div>
  <div class="info-item" style="top:488px">
    <div class="icon"><svg width="38" height="26" viewBox="0 0 38 26"><rect x="1" y="1" width="36" height="24" fill="#fff"/><path d="M1 1l18 14L37 1M1 25l13-12M37 25L24 13" fill="none" stroke="#00e1f5" stroke-width="2"/></svg></div>
    <div class="text"><strong>EMAIL US</strong>hello@brisalagoon.ch</div>
  </div>
</aside>

<section class="form-panel"></section>
<div class="field-label" style="left:595px;top:1335px">TELL US YOUR NAME *</div>
<div class="field" style="left:595px;top:1365px;width:222px">First Name</div>
<div class="field" style="left:838px;top:1365px;width:222px">Last Name</div>
<div class="field-label" style="left:595px;top:1439px">ENTER YOUR EMAIL *</div>
<div class="field-label" style="left:842px;top:1439px">ENTER YOUR PHONE NUMBER *</div>
<div class="field" style="left:595px;top:1469px;width:222px">Email</div>
<div class="field" style="left:838px;top:1469px;width:222px">Phone</div>
<div class="field-label" style="left:595px;top:1542px">TYPE OF POOL *</div>
<div class="field-label" style="left:842px;top:1542px">SIZE&nbsp; *</div>
<div class="field" style="left:595px;top:1571px;width:219px">Composite Wood Pools
  <svg class="abs" style="right:14px;top:17px" width="16" height="12" viewBox="0 0 16 12"><path d="M0 0h16L8 12z" fill="#666"/></svg></div>
<div class="field unit" style="left:843px;top:1571px;width:91px">m</div>
<div class="abs" style="left:949px;top:1584px;font-size:15px">x</div>
<div class="field unit" style="left:969px;top:1571px;width:91px">m</div>
<div class="field-label" style="left:595px;top:1646px">MESSAGE *</div>
<div class="field" style="left:595px;top:1675px;width:465px;height:151px">Write us a message</div>
<div class="btn submit">SUBMIT NOW<span class="arrow"><svg width="16" height="12" viewBox="0 0 16 12"><path d="M2 2l4 4-4 4M8 2l4 4-4 4" fill="none" stroke="#fff" stroke-width="2"/></svg></span></div>

<footer class="site-footer">
  <div class="footer-brand">BRISA<br>LAGOON</div>
  <div class="footer-col"><h3 style="left:398px">Quick Links</h3></div>
  <ul class="quick-links">
    <li style="top:140px">Home</li>
    <li style="top:167px">Our Products</li>
    <li style="top:194px">Our Projects</li>
    <li style="top:222px">Contact Us</li>
  </ul>
  <div class="footer-col"><h3 style="left:611px">Contact Us</h3></div>
  <div class="f-contact" style="left:611px;top:142px"><span class="box"><svg width="12" height="12" viewBox="0 0 36 36"><path d="M8 4l6 6-3 4c2 5 6 9 11 11l4-3 6 6-4 5C16 32 4 20 3 8z" fill="#fff"/></svg></span><span>CALL US<br>079 555 01 23</span></div>
  <div class="f-contact" style="left:611px;top:191px"><span class="box"><svg width="12" height="9" viewBox="0 0 38 26"><rect width="38" height="26" fill="#fff"/></svg></span><span>EMAIL US<br>hello@brisalagoon.ch</span></div>
  <div class="f-contact" style="left:611px;top:241px"><span class="box"><svg width="10" height="14" viewBox="0 0 30 40"><path d="M15 2C8 2 3 7 3 14c0 9 12 24 12 24s12-15 12-24C27 7 22 2 15 2z" fill="#fff"/></svg></span><span>Marco Lehner<br>Rue des Tilleuls 27<br>1860 Aigle</span></div>
  <div class="footer-col"><h3 style="left:886px;top:63px">Our Newsletter</h3></div>
  <div class="newsletter">
    <p>Subscribe our newsletter to get the latest news.</p>
    <div class="input"></div>
    <div class="sub">SUBSCRIBE</div>
  </div>
</footer>
<div class="bottom-bar">
  <p>Copyright © 2024 All Rights Reserved By Company name</p>
  <span class="social" style="left:989px"></span>
  <span class="social" style="left:1024px"></span>
  <span class="social" style="left:1060px"></span>
  <span class="social" style="left:1096px"></span>
</div>

</body>
</html>
```